Communication and Marketing agency needs a new presentation card

We are a group of communication and marketing agencies specialized in companies that are in the logistics and industrial sector. The head agency is TELVANO Grupo and the group consists of 4 agencies: TELVANO Media, TELVANO Digital, TELVANO Research and DifundeEnPantalla. We hace 4 offices in Spain (Madrid, Barcelona, Valencia and Murcia). We are looking for a clean and attractive design that transmits our experience, brand presence in the market and knowledge to those who receive the card.It has to maintain the colors of the logo that is attached.
Target Market(s)
logistics and industrial sector
Marketing department
Contact Information for Business Card
Clean and attractive design

```html
<!DOCTYPE html>
<html lang="en">
<head>
<meta charset="UTF-8">
<title>TELVANO Grupo – Business Card</title>
<link href="https://fonts.googleapis.com/css2?family=Montserrat:wght@400;500;700&display=swap" rel="stylesheet">
<style>
  :root {
    --bg: #4a4c4f;
    --card-back: #58595b;
    --card-front: #ffffff;
    --brand-red: #b3202a;
    --brand-grey: #4d4a48;
    --text-grey: #5a5a5a;
    --logo-light: #ececec;
  }
  * { margin: 0; padding: 0; box-sizing: border-box; }
  html, body { width: 1200px; height: 960px; overflow: hidden; }
  body {
    background: var(--bg);
    font-family: "Montserrat", sans-serif;
    position: relative;
  }
  .card {
    position: absolute;
    width: 620px;
    height: 354px;
    box-shadow: 0 14px 30px rgba(0,0,0,0.35);
    overflow: hidden;
  }
  /* Back side */
  .card-back {
    left: 90px; top: 90px;
    background: var(--card-back);
    display: grid;
    grid-template-columns: auto auto;
    grid-template-rows: auto auto;
    justify-content: center;
    align-content: center;
    gap: 48px 56px;
  }
  .agency-name {
    color: var(--logo-light);
    font-weight: 500;
    font-size: 23px;
    letter-spacing: 1px;
    line-height: 1.1;
    white-space: nowrap;
  }
  /* Front side */
  .card-front {
    left: 490px; top: 510px;
    background: var(--card-front);
  }
  .front-wave {
    position: absolute;
    left: 0; top: 0;
    width: 620px; height: 354px;
  }
  .brand-name {
    position: absolute;
    right: 40px; top: 46px;
    color: var(--brand-red);
    font-weight: 500;
    font-size: 32px;
    letter-spacing: 2px;
    white-space: nowrap;
  }
  .person {
    position: absolute;
    left: 40px; top: 78px;
  }
  .person-name {
    color: var(--brand-red);
    font-weight: 700;
    font-size: 22px;
    line-height: 1.2;
  }
  .person-title {
    color: var(--text-grey);
    font-weight: 400;
    font-size: 15px;
    margin-top: 2px;
  }
  .contact-list {
    position: absolute;
    left: 40px; top: 136px;
    list-style: none;
    color: var(--text-grey);
    font-size: 13px;
    line-height: 1.4;
  }
  .contact-item {
    display: flex;
    align-items: flex-start;
    gap: 10px;
    margin-bottom: 2px;
    white-space: nowrap;
  }
  .contact-item.address { margin-bottom: 10px; }
  .contact-icon { width: 14px; height: 14px; flex: none; margin-top: 2px; fill: var(--brand-red); }
</style>
</head>
<body>

  <section class="card card-back" aria-label="Back of business card">
    <div class="agency-name">TELVANO Media</div>
    <div class="agency-name">TELVANO Digital</div>
    <div class="agency-name">TELVANO Research</div>
    <div class="agency-name">DifundeEnPantalla</div>
  </section>

  <section class="card card-front" aria-label="Front of business card">
    <svg class="front-wave" viewBox="0 0 620 354" aria-hidden="true">
      <path d="M0 268 C 180 276, 340 250, 480 184 C 400 238, 240 288, 0 290 Z" fill="var(--brand-grey)"/>
      <path d="M0 298 C 220 298, 380 240, 500 186 C 560 160, 600 152, 620 150 L 620 354 L 0 354 Z" fill="var(--brand-red)"/>
    </svg>

    <div class="brand-name">TELVANO Grupo</div>

    <div class="person">
      <div class="person-name">Your Name</div>
      <div class="person-title">Your Title</div>
    </div>

    <ul class="contact-list">
      <li class="contact-item address">
        <svg class="contact-icon" viewBox="0 0 24 24"><path d="M12 2a7 7 0 0 0-7 7c0 5 7 13 7 13s7-8 7-13a7 7 0 0 0-7-7zm0 9.5A2.5 2.5 0 1 1 12 6.5a2.5 2.5 0 0 1 0 5z"/></svg>
        <span>Your address, city<br>state, ZIP 0000</span>
      </li>
      <li class="contact-item">
        <svg class="contact-icon" viewBox="0 0 24 24"><path d="M6.6 10.8a15 15 0 0 0 6.6 6.6l2.2-2.2a1 1 0 0 1 1-.25 11.4 11.4 0 0 0 3.6.57 1 1 0 0 1 1 1V20a1 1 0 0 1-1 1A17 17 0 0 1 3 4a1 1 0 0 1 1-1h3.5a1 1 0 0 1 1 1c0 1.250.2 2.450.57 3.6a1 1 0 0 1-.25 1z"/></svg>
        <span>123-456-2100</span>
      </li>
      <li class="contact-item">
        <svg class="contact-icon" viewBox="0 0 24 24"><path d="M2 5h20v14H2z M2 5l10 8 10-8" fill="none" stroke="var(--brand-red)" stroke-width="2.4"/></svg>
        <span>youremail@mailbox.com</span>
      </li>
      <li class="contact-item">
        <svg class="contact-icon" viewBox="0 0 24 24"><circle cx="12" cy="12" r="9" fill="none" stroke="var(--brand-red)" stroke-width="2.4"/><path d="M3 12h18M12 3c3 3 3 15 0 18M12 3c-3 3-3 15 0 18" fill="none" stroke="var(--brand-red)" stroke-width="1.8"/></svg>
        <span>www.yourwebsite.com</span>
      </li>
    </ul>
  </section>

</body>
</html>
```